Professional Photography Business cards

I need business cards that include my logo which I have uploaded. I run a photography business. I am open to ideas but I would like one side to have my logo and the other side to have my contact info. I don't have a website made but I do own a website domain. I have uploaded 2 different logo color schemes. My business colors are Blue, black , and white.

Business Name
Business Phone Number
Business Email
Business Website address
Instagram

Industry/Entity Type

Professional Photography

Contact Information for Business Card

Phone Number: 916-384-7702 email: info@tlane-studio.example Instagram: @t.lanestudio website doman- www.tlane-studio.example

Requirements
Must have
• I like the idea of a business card with a full black background front and back of card. My colors must include royal blue, black, and white

```html
<!DOCTYPE html>
<html lang="en">
<head>
<meta charset="UTF-8">
<title>T. Lane Studio — Business Card</title>
<link rel="stylesheet" href="https://fonts.googleapis.com/css2?family=Playfair+Display:wght@400&display=swap">
<style>
  :root {
    --backdrop: #9c9a9a;
    --backdrop-edge: #6a6868;
    --card-black: #000000;
    --card-white: #ffffff;
    --ink: #111111;
    --royal: #27288e;
    --mark-dark: #2b2b2b;
    --mark-light: #e3e3e3;
  }
  * { margin: 0; padding: 0; box-sizing: border-box; }
  html, body {
    width: 1200px;
    height: 1200px;
    overflow: hidden;
  }
  body {
    background: radial-gradient(ellipse at 30% 40%, #b4b2b2 0%, var(--backdrop) 45%, var(--backdrop-edge) 100%);
    font-family: "Playfair Display", Georgia, serif;
    position: relative;
  }
  .card {
    position: absolute;
    width: 460px;
    height: 720px;
    box-shadow: 0 8px 20px rgba(0,0,0,0.35);
    overflow: hidden;
  }
  .card--front {
    left: 90px;
    top: 200px;
    background: var(--card-black);
  }
  .card--back {
    left: 650px;
    top: 300px;
    background: var(--card-white);
  }
  .faint-mark {
    position: absolute;
    width: 200px;
    height: 200px;
    border-radius: 50%;
    border: 14px solid var(--mark-dark);
  }
  .card--front .faint-mark { left: 160px; top: 100px; }
  .card--back .faint-mark { left: 240px; top: 520px; border-color: var(--mark-light); }
  .wordmark {
    position: absolute;
    left: 0;
    right: 0;
    display: flex;
    align-items: center;
    justify-content: center;
    gap: 14px;
    font-size: 38px;
    font-weight: 400;
    letter-spacing: 0.02em;
  }
  .card--front .wordmark { top: 330px; color: var(--card-white); }
  .card--back .wordmark { top: 110px; color: var(--royal); }
  .wordmark__dot {
    width: 18px;
    height: 18px;
    border-radius: 50%;
    background: currentColor;
  }
  .contact {
    position: absolute;
    left: 0;
    right: 0;
    top: 270px;
    list-style: none;
    display: flex;
    flex-direction: column;
    align-items: center;
    gap: 30px;
    color: var(--ink);
  }
  .contact__item {
    display: flex;
    align-items: center;
    gap: 14px;
    font-size: 20px;
  }
  .contact__item--phone { font-size: 30px; margin-bottom: 4px; }
  .contact__icon {
    width: 20px;
    height: 20px;
    flex: none;
    stroke: var(--royal);
    fill: none;
    stroke-width: 1.6;
  }
  .contact__square {
    width: 18px;
    height: 18px;
    border: 2px solid var(--royal);
    border-radius: 4px;
    flex: none;
  }
</style>
</head>
<body>
  <section class="card card--front">
    <div class="faint-mark" aria-hidden="true"></div>
    <div class="wordmark"><span class="wordmark__dot"></span>T. Lane Studio</div>
  </section>

  <section class="card card--back">
    <div class="wordmark"><span class="wordmark__dot"></span>T. Lane Studio</div>
    <ul class="contact">
      <li class="contact__item contact__item--phone">
        <svg class="contact__icon" viewBox="0 0 24 24" aria-hidden="true">
          <path d="M5 3h4l2 5-2.5 1.5a11 11 0 0 0 6 6L16 13l5 2v4a2 2 0 0 1-2 2A17 17 0 0 1 3 5a2 2 0 0 1 2-2z"/>
        </svg>
        916-384-7702
      </li>
      <li class="contact__item">
        <svg class="contact__icon" viewBox="0 0 24 24" aria-hidden="true">
          <rect x="2" y="5" width="20" height="14"/>
          <path d="M2 5l10 8 10-8M2 19l7-7M22 19l-7-7"/>
        </svg>
        info@tlane-studio.example
      </li>
      <li class="contact__item">
        <span class="contact__square" aria-hidden="true"></span>
        @t.lanestudio
      </li>
      <li class="contact__item">
        <svg class="contact__icon" viewBox="0 0 24 24" aria-hidden="true">
          <circle cx="12" cy="12" r="9"/>
          <ellipse cx="12" cy="12" rx="4" ry="9"/>
          <path d="M3 12h18M5 7h14M5 17h14"/>
        </svg>
        www.tlane-studio.example
      </li>
    </ul>
    <div class="faint-mark" aria-hidden="true"></div>
  </section>
</body>
</html>
```